Healthcare and Professional IT Services Company need a redesigned business card

We are a IT Services company that targets small medical practices and professional business such as Attorneys, Accounts, Architects etc. We want to communicate a professional yet friendly image using recent logo redesign here on ArtHarbor. Like to see the colors blue and orange in the design. Must use the Tall Pine Computing as displayed in the new logo - then also want to incorporate the fish logo as well.

Target Market(s)

Small medical and professional services

Industry/Entity Type

It Company

Contact Information for Business Card

The usual stuff, place for name address phone website. Also maybe our tagline which is "rooted in technology"

Requirements
Must have
• My new logo and the fish somewhere on the card

```html
<!DOCTYPE html>
<html lang="en">
<head>
<meta charset="utf-8">
<title>Tall Pine Computing – Business Card</title>
<link rel="stylesheet" href="https://fonts.googleapis.com/css2?family=Montserrat:wght@400;500;700&display=swap">
<style>
  :root {
    --page: #e9ecef;
    --card-white: #f7f8f8;
    --blue-light: #1ba6df;
    --blue-mid: #1590d2;
    --blue-deep: #0b74bd;
    --orange: #f3a81c;
    --logo-blue: #25a4dc;
    --text-light: #ffffff;
    --tagline-blue: #3f9bd6;
  }
  * { box-sizing: border-box; margin: 0; padding: 0; }
  html, body {
    width: 1200px; height: 780px; overflow: hidden;
    background: var(--page);
    font-family: "Montserrat", sans-serif;
  }
  .canvas {
    width: 1200px; height: 780px;
    display: flex; align-items: center; justify-content: center; gap: 40px;
  }
  .card {
    position: relative;
    width: 540px; height: 309px;
    border-radius: 4px;
    overflow: hidden;
    box-shadow: 0 6px 18px rgba(0,0,0,.18);
  }
  /* Front */
  .card-front { background: var(--card-white); }
  .front-shape { position: absolute; inset: 0; width: 100%; height: 100%; }
  .front-logo {
    position: absolute; left: 34px; top: 110px; width: 210px;
    display: flex; flex-direction: column; align-items: flex-start; gap: 10px;
  }
  .brand-row { display: flex; align-items: center; gap: 10px; }
  .brand-dot { width: 16px; height: 16px; border-radius: 50%; background: var(--orange); flex: none; }
  .brand-name {
    font-weight: 700; font-size: 24px; line-height: 1.05; color: var(--logo-blue);
    letter-spacing: -0.3px;
  }
  .tagline { font-size: 13px; color: var(--tagline-blue); letter-spacing: .3px; padding-left: 26px; }
  .contact {
    position: absolute; left: 300px; top: 48px; color: var(--text-light);
  }
  .contact-name { font-weight: 700; font-size: 19px; letter-spacing: -.2px; }
  .contact-role { font-size: 12px; margin-top: 2px; }
  .contact-lines { margin-top: 26px; font-size: 12.5px; line-height: 1.55; list-style: none; }
  .contact-lines li { display: flex; align-items: center; gap: 6px; }
  .icon { width: 13px; height: 13px; flex: none; }
  .contact-web { margin-top: 18px; font-size: 12.5px; }
  /* Back */
  .card-back {
    background: radial-gradient(ellipse at 40% 40%, var(--blue-light) 0%, var(--blue-mid) 55%, var(--blue-deep) 100%);
    display: flex; flex-direction: column; align-items: center; justify-content: center; gap: 14px;
  }
  .card-back .brand-dot { width: 22px; height: 22px; background: var(--text-light); }
  .card-back .brand-name { color: var(--text-light); font-size: 36px; }
  .card-back .tagline { color: var(--text-light); font-size: 15px; letter-spacing: 4px; padding-left: 0; }
</style>
</head>
<body>
<main class="canvas">
  <section class="card card-front" aria-label="Business card front">
    <svg class="front-shape" viewBox="0 0 540 309" preserveAspectRatio="none" aria-hidden="true">
      <defs>
        <linearGradient id="blueFade" x1="0" y1="0" x2="1" y2="1">
          <stop offset="0" stop-color="#21aee3"/>
          <stop offset="1" stop-color="#0d7ec4"/>
        </linearGradient>
      </defs>
      <path d="M210 0 C 250 70, 230 140, 250 200 C 265 250, 250 290, 262 309 L540 309 L540 0 Z" fill="#f3a81c"/>
      <path d="M218 0 C 258 70, 238 140, 258 200 C 273 250, 258 290, 270 309 L540 309 L540 0 Z" fill="url(#blueFade)"/>
    </svg>
    <div class="front-logo">
      <div class="brand-row">
        <span class="brand-dot"></span>
        <span class="brand-name">Tall Pine Computing</span>
      </div>
      <span class="tagline">rooted in technology</span>
    </div>
    <div class="contact">
      <p class="contact-name">Employee Name</p>
      <p class="contact-role">Director</p>
      <ul class="contact-lines">
        <li>P.O. Box 000</li>
        <li>Cedar Ridge, 2nd Lane, USA</li>
        <li>
          <svg class="icon" viewBox="0 0 14 14" aria-hidden="true"><rect width="14" height="14" rx="2" fill="#fff"/><path d="M4 3.5 l2 0 l.8 2.2 l-1.2 .9 a6 6 0 0 0 2.8 2.8 l.9-1.2 l2.2.8 l0 2 a1 1 0 0 1 -1 1 a8 8 0 0 1 -7.5 -7.5 a1 1 0 0 1 1 -1z" fill="#1590d2"/></svg>
          0100 555 210
        </li>
        <li>
          <svg class="icon" viewBox="0 0 14 14" aria-hidden="true"><rect width="14" height="14" rx="2" fill="#fff"/><rect x="3" y="4" width="8" height="6" fill="none" stroke="#1590d2" stroke-width="1.2"/><path d="M3 4 l4 3.5 l4 -3.5" fill="none" stroke="#1590d2" stroke-width="1.2"/></svg>
          hello@tallpinemail.com
        </li>
      </ul>
      <p class="contact-web">www.tallpinecomputing.com</p>
    </div>
  </section>

  <section class="card card-back" aria-label="Business card back">
    <div class="brand-row">
      <span class="brand-dot"></span>
      <span class="brand-name">Tall Pine Computing</span>
    </div>
    <span class="tagline">rooted in technology</span>
  </section>
</main>
</body>
</html>
```